Business Card Design for Software Development Company

I am looking for a business card design the incorporates my new logo (attached below).

Key information to include:
Name: Martin Quelbrook
Title: CEO
Email: martin@brightwellcivic.example
Phone: 555-218-9403
Website: www.brightwellcivic.example

NOTE: This design should be easy to edit so that we can order cards for different members of our team.

```html
<!DOCTYPE html>
<html lang="en">
<head>
<meta charset="utf-8">
<title>BrightwellLabs Business Cards</title>
<link href="https://fonts.googleapis.com/css2?family=Montserrat:wght@400;700&display=swap" rel="stylesheet">
<style>
  :root {
    --backdrop: #ced3d2;
    --paper: #efefec;
    --navy: #2f3650;
    --teal: #1fb49b;
    --ink: #3a3f4a;
  }
  * { box-sizing: border-box; margin: 0; padding: 0; }
  html, body { width: 1200px; height: 881px; overflow: hidden; }
  body {
    background: var(--backdrop);
    font-family: "Montserrat", sans-serif;
    display: flex;
    align-items: center;
    justify-content: center;
    gap: 60px;
  }
  .card {
    position: relative;
    width: 500px;
    height: 286px;
    background: var(--paper);
    border-bottom: 5px solid var(--teal);
    box-shadow: 0 18px 30px rgba(0,0,0,0.18);
  }
  .brand {
    position: absolute;
    display: flex;
    align-items: center;
    gap: 10px;
  }
  .brand-mark {
    width: 30px;
    height: 30px;
    background: var(--teal);
    flex: none;
  }
  .brand-name {
    font-weight: 700;
    font-size: 44px;
    letter-spacing: -1px;
    color: var(--navy);
    line-height: 1;
  }
  .brand-tagline {
    position: absolute;
    font-weight: 700;
    font-size: 6.5px;
    letter-spacing: 0.6px;
    color: var(--navy);
    text-transform: uppercase;
  }
  .card-front .brand { left: 34px; top: 44px; }
  .card-front .brand-tagline { right: 38px; top: 102px; }
  .card-back .brand { left: 34px; top: 118px; }
  .card-back .brand-tagline { right: 38px; top: 176px; }

  .holder {
    position: absolute;
    right: 262px;
    top: 170px;
    text-align: right;
  }
  .holder-name {
    font-weight: 700;
    font-size: 19px;
    color: var(--teal);
  }
  .holder-title {
    font-weight: 400;
    font-size: 13px;
    color: var(--ink);
    margin-top: 4px;
  }
  .divider {
    position: absolute;
    left: 252px;
    top: 168px;
    width: 1.5px;
    height: 70px;
    background: var(--teal);
  }
  .contact {
    position: absolute;
    left: 268px;
    top: 176px;
    list-style: none;
  }
  .contact li {
    display: flex;
    align-items: center;
    gap: 7px;
    font-size: 12px;
    color: var(--ink);
    line-height: 1;
    margin-bottom: 8px;
  }
  .contact svg { width: 10px; height: 10px; flex: none; fill: var(--teal); }
</style>
</head>
<body>
  <section class="card card-front">
    <div class="brand">
      <span class="brand-mark"></span>
      <span class="brand-name">BrightwellLabs</span>
    </div>
    <p class="brand-tagline">A division of Brightwell Civic</p>

    <div class="holder">
      <p class="holder-name">Martin Quelbrook</p>
      <p class="holder-title">CEO</p>
    </div>
    <span class="divider"></span>
    <ul class="contact">
      <li>
        <svg viewBox="0 0 10 10" aria-hidden="true"><path d="M2 0.5 L3.6 0.5 L4.2 2.8 L3.1 3.6 Q4 5.7 6.4 6.9 L7.2 5.8 L9.5 6.4 L9.5 8 Q9.3 9.5 7.8 9.5 Q0.5 8.5 0.5 2 Q0.5 0.5 2 0.5Z"/></svg>
        555-218-9403
      </li>
      <li>
        <svg viewBox="0 0 10 10" aria-hidden="true"><path d="M0.5 2 H9.5 V8.5 H0.5Z M1.2 2.6 L5 5.6 L8.8 2.6 V3.4 L5 6.4 L1.2 3.4Z" fill-rule="evenodd"/></svg>
        martin@brightwellcivic.example
      </li>
      <li>
        <svg viewBox="0 0 10 10" aria-hidden="true"><circle cx="5" cy="5" r="4.5"/></svg>
        www.brightwellcivic.example
      </li>
    </ul>
  </section>

  <section class="card card-back">
    <div class="brand">
      <span class="brand-mark"></span>
      <span class="brand-name">BrightwellLabs</span>
    </div>
    <p class="brand-tagline">A division of Brightwell Civic</p>
  </section>
</body>
</html>
```